Kestrel Facilities Business Card Design

We would now like to design business cards with the new Kestrel Facilities logo

Target Market(s)

Professional

Industry/Entity Type

Professional services

Contact Information for Business Card

Employee name, title, phone number, email address, corporate office address and logo.

Font styles to use
Sans Serif

Colors
0054AA
0677BA
7BADD7
CADEEF
E8F1F8

Requirements
Must have
• My logo
Should not have
• any other pictures or images besides my logo

```html
<!DOCTYPE html>
<html lang="en">
<head>
<meta charset="utf-8">
<title>Kestrel Facilities Business Card</title>
<link href="https://fonts.googleapis.com/css2?family=Montserrat:wght@400;500;700;800&display=swap" rel="stylesheet">
<style>
  :root {
    --brand-blue: #3676be;
    --brand-deep: #0054aa;
    --pale-blue: #cadeef;
    --mist: #e8f1f8;
    --ink: #1c1c1c;
    --white: #ffffff;
    --stage: #e4e7eb;
  }
  * { margin: 0; padding: 0; box-sizing: border-box; }
  html, body { width: 1200px; height: 900px; overflow: hidden; }
  body {
    background: var(--stage);
    font-family: "Montserrat", sans-serif;
    position: relative;
  }
  .card {
    position: absolute;
    left: 320px;
    width: 560px;
    height: 320px;
    border-radius: 22px;
    overflow: hidden;
    box-shadow: 0 8px 24px rgba(0,0,0,0.18);
  }
  .card-front { top: 110px; background: var(--white); }
  .card-back { top: 470px; background: var(--brand-blue); }

  .wave { position: absolute; inset: 0; width: 100%; height: 100%; }

  .contact-block {
    position: absolute;
    left: 38px;
    top: 54px;
    color: var(--ink);
  }
  .person-name {
    font-weight: 800;
    font-size: 21px;
    color: var(--brand-blue);
    letter-spacing: 0.3px;
    text-transform: uppercase;
  }
  .person-title {
    font-size: 14px;
    font-weight: 500;
    margin-top: 4px;
  }
  .address {
    font-size: 13.5px;
    font-weight: 500;
    line-height: 1.45;
    margin-top: 14px;
  }
  .contact-list {
    list-style: none;
    margin-top: 12px;
    font-size: 13.5px;
    font-weight: 500;
    line-height: 1.65;
  }
  .contact-list li { display: flex; align-items: center; gap: 8px; }
  .contact-list svg { width: 14px; height: 14px; fill: var(--brand-blue); flex: none; }

  .brand-mark {
    position: absolute;
    display: flex;
    align-items: center;
    gap: 12px;
    font-weight: 700;
    text-transform: uppercase;
    line-height: 1;
    white-space: nowrap;
  }
  .brand-mark .brand-square {
    width: 30px; height: 30px;
    border: 5px solid currentColor;
    flex: none;
  }
  .card-front .brand-mark {
    right: 34px; bottom: 28px;
    font-size: 24px;
    color: var(--brand-blue);
  }
  .card-back .brand-mark {
    left: 50%; top: 50%;
    transform: translate(-50%, -50%);
    font-size: 36px;
    color: var(--pale-blue);
  }
  .card-back .brand-mark .brand-square { width: 46px; height: 46px; border-width: 8px; }
</style>
</head>
<body>

  <section class="card card-front" aria-label="Business card front">
    <svg class="wave" viewBox="0 0 560 320" preserveAspectRatio="none" aria-hidden="true">
      <path d="M150,0 C270,6 305,75 355,140 C395,190 460,206 560,208 L560,0 Z" fill="var(--brand-blue)"/>
      <path d="M120,22 C255,26 300,100 345,160 C385,210 450,222 560,224" fill="none" stroke="var(--brand-blue)" stroke-width="5"/>
    </svg>

    <div class="contact-block">
      <h1 class="person-name">Dana Whitfield</h1>
      <p class="person-title">Co-Founder</p>
      <p class="address">4180 N. Harbor Lane<br>Suite 2210 Eastfield.14</p>
      <ul class="contact-list">
        <li>
          <svg viewBox="0 0 24 24"><path d="M6.6 10.8a15 15 0 0 0 6.6 6.6l2.2-2.2c.3-.3.7-.4 1-.2 1.1.4 2.3.6 3.6.6.6 0 1 .4 1 1V20c0 .6-.4 1-1 1A17 17 0 0 1 3 4c0-.6.4-1 1-1h3.5c.6 0 1 .4 1 1 0 1.3.2 2.5.6 3.6.1.3 0 .7-.2 1z"/></svg>
          +254-300-41725
        </li>
        <li>
          <svg viewBox="0 0 24 24"><path d="M2 5h20v14H2z M2 5l10 8 10-8" fill="none" stroke="var(--brand-blue)" stroke-width="2"/></svg>
          hello@kestrelfacilities.com
        </li>
        <li>
          <svg viewBox="0 0 24 24"><circle cx="12" cy="12" r="10"/><path d="M2 12h20M12 2c3 3 3 17 0 20M12 2c-3 3-3 17 0 20" fill="none" stroke="#fff" stroke-width="1.5"/></svg>
          www.kestrelfacilities.com
        </li>
      </ul>
    </div>

    <div class="brand-mark">
      <span class="brand-square"></span>
      <span class="brand-name">Kestrel Facilities</span>
    </div>
  </section>

  <section class="card card-back" aria-label="Business card back">
    <div class="brand-mark">
      <span class="brand-square"></span>
      <span class="brand-name">Kestrel Facilities</span>
    </div>
  </section>

</body>
</html>
```